Coffeeshop menu for filter tip

We want to have a cannabis (coffeeshop) menu in the size 25mm wide x 60mm wide. Some examples attached.

it must have the following text:
Menu

WEED p/g
Oblivane €16
Cloudplum €14
Tide Runner €14
Quincefig €16
Mega Marsh €14
Grey Heron €14

HASH p/g
Tashar Amber €12
Pebble Frost€11
Lime Dunes €14
Ash Petal €10

Target Market(s)

tourist in Amsterdam

Requirements
Nice to have
• cannabis sign leaf
• No Cigarettes allowed symbol

```html
<!DOCTYPE html>
<html lang="en">
<head>
<meta charset="UTF-8">
<title>Coffeeshop Menu</title>
<link rel="stylesheet" href="https://fonts.googleapis.com/css2?family=Exo+2:wght@500;600&family=Quicksand:wght@600;700&display=swap">
<style>
  :root {
    --bg-top: #0c130e;
    --bg-mid: #12301a;
    --bg-bottom: #1f7a30;
    --leaf-bright: rgba(60, 220, 70, 0.32);
    --leaf-dark: rgba(0, 0, 0, 0.28);
    --accent: #3ddc3d;
    --accent-line: #35c93a;
    --tab-text: #0d1a0f;
    --price: #ffffff;
    --heading: #d9dcd9;
    --unit: #b9c2bb;
    --panel: rgba(8, 18, 10, 0.55);
    --sign-red: #d8251f;
  }
  * { box-sizing: border-box; margin: 0; padding: 0; }
  html, body { width: 1200px; height: 2892px; overflow: hidden; }
  body {
    position: relative;
    background: linear-gradient(180deg, var(--bg-top) 0%, var(--bg-mid) 45%, var(--bg-bottom) 100%);
    font-family: "Quicksand", sans-serif;
  }
  .leaf-art { position: absolute; border-radius: 50%; }
  .leaf-art--top-right { left: 520px; top: -60px; width: 760px; height: 860px;
    background: radial-gradient(ellipse at 55% 45%, var(--leaf-bright), transparent 68%); }
  .leaf-art--left { left: -160px; top: 520px; width: 620px; height: 720px;
    background: radial-gradient(ellipse at 45% 50%, var(--leaf-bright), transparent 66%); }
  .leaf-art--middle { left: 460px; top: 940px; width: 780px; height: 880px;
    background: radial-gradient(ellipse at 50% 50%, var(--leaf-dark), transparent 68%); }
  .leaf-art--bottom-left { left: -180px; top: 1820px; width: 860px; height: 1200px;
    background: radial-gradient(ellipse at 40% 50%, var(--leaf-bright), transparent 66%); }

  .menu-title {
    position: absolute; left: 92px; top: 100px;
    font-family: "Exo 2", sans-serif; font-weight: 600;
    font-size: 176px; line-height: 1; letter-spacing: 6px;
    color: var(--heading);
  }

  .price-panel {
    position: absolute; left: 139px; width: 914px;
    border: 3px solid var(--accent-line);
    background: var(--panel);
  }
  .price-panel--weed { top: 483px; height: 1160px; }
  .price-panel--hash { top: 1735px; height: 781px; }

  .panel-tab {
    position: absolute; left: -3px; top: -3px;
    width: 324px; height: 72px;
    background: var(--accent);
    color: var(--tab-text);
    font-family: "Exo 2", sans-serif; font-weight: 600;
    font-size: 58px; line-height: 72px; letter-spacing: 3px;
    padding-left: 28px;
  }
  .panel-unit {
    position: absolute; right: 104px; top: 44px;
    font-family: "Exo 2", sans-serif; font-weight: 500;
    font-size: 46px; color: var(--unit); letter-spacing: 2px;
  }

  .price-list { position: absolute; left: 63px; right: 52px; list-style: none; }
  .price-panel--weed .price-list { top: 170px; }
  .price-panel--hash .price-list { top: 170px; }
  .price-row {
    display: flex; align-items: baseline;
    height: 149px; line-height: 90px;
  }
  .price-panel--hash .price-row { height: 149px; }
  .item-name {
    font-weight: 700; font-size: 58px; letter-spacing: 1px;
    color: var(--accent); text-transform: uppercase; white-space: nowrap;
  }
  .item-leader {
    flex: 1; border-bottom: 2px solid rgba(61, 220, 61, 0.55);
    margin: 0 22px 0 14px; transform: translateY(-6px);
  }
  .item-price {
    font-weight: 700; font-size: 62px; color: var(--price); white-space: nowrap;
  }

  .no-cigarettes {
    position: absolute; left: 856px; top: 2632px; width: 254px; height: 202px;
    border: 5px solid var(--sign-red); border-radius: 14px;
    background: rgba(0, 0, 0, 0.35);
  }
  .no-cigarettes svg { position: absolute; left: 0; top: 0; }
  .no-cigarettes__label {
    position: absolute; left: 0; right: 0; bottom: 18px; text-align: center;
    font-family: "Exo 2", sans-serif; font-weight: 600;
    font-size: 30px; letter-spacing: 1px; color: #111;
  }
</style>
</head>
<body>
  <div class="leaf-art leaf-art--top-right" role="img" aria-label="Large cannabis leaf outline decoration"></div>
  <div class="leaf-art leaf-art--left" role="img" aria-label="Cannabis leaf outline decoration"></div>
  <div class="leaf-art leaf-art--middle" role="img" aria-label="Dark cannabis leaf silhouette decoration"></div>
  <div class="leaf-art leaf-art--bottom-left" role="img" aria-label="Cannabis leaf decoration"></div>

  <h1 class="menu-title">MENU</h1>

  <section class="price-panel price-panel--weed">
    <h2 class="panel-tab">WEED</h2>
    <span class="panel-unit">P/G</span>
    <ul class="price-list">
      <li class="price-row"><span class="item-name">Oblivane</span><span class="item-leader"></span><span class="item-price">€16</span></li>
      <li class="price-row"><span class="item-name">Cloudplum</span><span class="item-leader"></span><span class="item-price">€14</span></li>
      <li class="price-row"><span class="item-name">Tide Runner</span><span class="item-leader"></span><span class="item-price">€14</span></li>
      <li class="price-row"><span class="item-name">Quincefig</span><span class="item-leader"></span><span class="item-price">€16</span></li>
      <li class="price-row"><span class="item-name">Mega Marsh</span><span class="item-leader"></span><span class="item-price">€14</span></li>
      <li class="price-row"><span class="item-name">Grey Heron</span><span class="item-leader"></span><span class="item-price">€14</span></li>
    </ul>
  </section>

  <section class="price-panel price-panel--hash">
    <h2 class="panel-tab">HASH</h2>
    <span class="panel-unit">P/G</span>
    <ul class="price-list">
      <li class="price-row"><span class="item-name">Tashar Amber</span><span class="item-leader"></span><span class="item-price">€12</span></li>
      <li class="price-row"><span class="item-name">Pebble Frost</span><span class="item-leader"></span><span class="item-price">€11</span></li>
      <li class="price-row"><span class="item-name">Lime Dunes</span><span class="item-leader"></span><span class="item-price">€14</span></li>
      <li class="price-row"><span class="item-name">Ash Petal</span><span class="item-leader"></span><span class="item-price">€10</span></li>
    </ul>
  </section>

  <div class="no-cigarettes" aria-label="No cigarettes">
    <svg width="244" height="192" viewBox="0 0 244 192" aria-hidden="true">
      <text x="30" y="122" font-family="Exo 2, sans-serif" font-weight="600" font-size="120" fill="#111">N</text>
      <circle cx="150" cy="80" r="50" fill="none" stroke="#111" stroke-width="10"/>
      <rect x="118" y="72" width="64" height="16" fill="#111"/>
      <line x1="117" y1="47" x2="183" y2="113" stroke="var(--sign-red)" stroke-width="10"/>
    </svg>
    <span class="no-cigarettes__label">CIGARETTES</span>
  </div>
</body>
</html>
```